Business Card for beauty technology startup

Design Glimora Business Card for a Beauty, based on the website identity and colors (https://www.glimora-example.com).
Glimora is a beauty tech startup that gathers helpful product info for beauty lovers and consumers (such as availability on stores, price range and product reviews) for makeup products. The card design must be young, colorful but clean, and very modern.

Target Market(s)

woman, 15-35

Industry/Entity Type

Cosmetics

Contact Information for Business Card

Full Name, address, phone

Font styles to use
Other font styles liked:
• Advent Pro

Colors
e34297
86cfc6
ffffff
5c5c5c
e8e8e8
e667a6
b2b2b2

Requirements
Must have
• One full colored side with a creative design and another with card info
• Use Color palette: #95C5C5 and/or #D38AA5
• Use fonts: Advent Pro
• Use website identity: https://www.glimora-example.com
Nice to have
• If needed extra font: Roboto

```html
<!DOCTYPE html>
<html lang="en">
<head>
<meta charset="utf-8">
<title>Glimora Business Card</title>
<link href="https://fonts.googleapis.com/css2?family=Advent+Pro:wght@300;400&family=Roboto:wght@400;500&display=swap" rel="stylesheet">
<style>
  :root {
    --stage: #dcdcdc;
    --paper: #f7f7f7;
    --rose: #b87a90;
    --rose-dark: #a86a82;
    --slate-light: #9a9a9a;
    --slate-dark: #6f6f6f;
    --ink: #1a1b1d;
    --white: #ffffff;
  }
  * { box-sizing: border-box; margin: 0; padding: 0; }
  html, body { width: 1200px; height: 960px; overflow: hidden; }
  body {
    background: var(--stage);
    position: relative;
    font-family: "Roboto", Arial, sans-serif;
  }
  .card {
    position: absolute;
    width: 600px;
    height: 342px;
    border-radius: 18px;
    overflow: hidden;
  }
  .card--front { left: 315px; top: 113px; background: var(--paper); }
  .card--back { left: 311px; top: 472px; background: var(--ink); }

  .brand {
    position: absolute;
    left: 0; right: 0; top: 72px;
    display: flex; align-items: center; justify-content: center; gap: 22px;
  }
  .brand__dot {
    width: 70px; height: 70px; border-radius: 50%;
    border: 2px solid var(--rose);
  }
  .brand__name {
    font-family: "Advent Pro", sans-serif;
    font-weight: 300;
    font-size: 58px;
    letter-spacing: 5px;
    color: var(--rose);
    line-height: 1;
  }

  .band {
    position: absolute; left: 0; right: 0; bottom: 0; height: 145px;
    background: linear-gradient(90deg, var(--slate-light) 0%, var(--slate-dark) 40%, var(--rose) 40%, var(--rose) 100%);
  }
  .band__disc {
    position: absolute; left: 222px; top: -3px;
    width: 150px; height: 150px; border-radius: 50%;
    background: var(--rose);
    border: 4px solid var(--white);
  }
  .person {
    position: absolute; left: 28px; top: 30px; color: var(--white);
  }
  .person__name { font-size: 20px; font-weight: 500; letter-spacing: 0.3px; }
  .person__role { font-size: 15px; margin-top: 4px; }
  .person__address { font-size: 14.5px; line-height: 19px; margin-top: 12px; }

  .contacts {
    position: absolute; right: 22px; top: 36px;
    list-style: none; color: var(--white); font-size: 14px;
  }
  .contacts li {
    display: flex; align-items: center; justify-content: flex-end; gap: 10px;
    height: 19.5px;
  }
  .contacts svg { width: 14px; height: 14px; fill: var(--white); }

  .back-brand {
    position: absolute; left: 405px; top: 222px;
    display: flex; align-items: center; gap: 10px;
  }
  .back-brand__dot {
    width: 30px; height: 30px; border-radius: 50%;
    border: 2px solid var(--rose);
  }
  .back-brand__name {
    font-family: "Advent Pro", sans-serif; font-weight: 300;
    font-size: 28px; letter-spacing: 2px; color: var(--rose);
  }
  .back-url {
    position: absolute; left: 400px; top: 295px;
    font-size: 12.5px; letter-spacing: 1.2px; color: var(--white);
  }
</style>
</head>
<body>

<section class="card card--front" aria-label="Card front">
  <div class="brand">
    <span class="brand__dot"></span>
    <span class="brand__name">GLIMORA</span>
  </div>

  <div class="band">
    <div class="band__disc"></div>
    <div class="person">
      <p class="person__name">MARA ELLISON</p>
      <p class="person__role">CEO/FOUNDER</p>
      <p class="person__address">4120 Linden Court<br>Fairbanks, Alaska 34610</p>
    </div>
    <ul class="contacts">
      <li>555 210 4837
        <svg viewBox="0 0 24 24" aria-hidden="true"><path d="M6.6 10.8a15 15 0 0 0 6.6 6.6l2.2-2.2c.3-.3.7-.4 1-.2 1.1.4 2.3.6 3.6.6.6 0 1 .4 1 1V20c0 .6-.4 1-1 1A17 17 0 0 1 3 4c0-.6.4-1 1-1h3.5c.6 0 1 .4 1 1 0 1.3.2 2.5.6 3.6.1.3 0 .7-.2 1z"/></svg>
      </li>
      <li>555 318 6072
        <svg viewBox="0 0 24 24" aria-hidden="true"><path d="M7 1h10a2 2 0 0 1 2 2v18a2 2 0 0 1-2 2H7a2 2 0 0 1-2-2V3a2 2 0 0 1 2-2zm0 3v14h10V4zm5 15.5a1 1 0 1 0 0 2 1 1 0 0 0 0-2z"/></svg>
      </li>
      <li>555 742 0195
        <svg viewBox="0 0 24 24" aria-hidden="true"><path d="M6 2h12v5H6zM3 8h18a2 2 0 0 1 2 2v7h-4v5H5v-5H1v-7a2 2 0 0 1 2-2zm4 8v4h10v-4z"/></svg>
      </li>
      <li>info@glimora-example.com
        <svg viewBox="0 0 24 24" aria-hidden="true"><path d="M2 5h20v14H2zm2 2v.5l8 5 8-5V7l-8 5z"/></svg>
      </li>
    </ul>
  </div>
</section>

<section class="card card--back" aria-label="Card back">
  <div class="back-brand">
    <span class="back-brand__dot"></span>
    <span class="back-brand__name">GLIMORA</span>
  </div>
  <p class="back-url">www.glimora-example.com</p>
</section>

</body>
</html>
```